Design a large parking banner – mandatory ticket validation in the shop

Banner Size:
548 cm (width) x 154 cm (height)
Note: The banner will be placed in a metal frame at our parking lot entrance, fully visible to every incoming truck driver. The message must be easy to read from a distance.
Goal of the Banner:
To inform all truck drivers that they must validate their entry ticket inside the shop, even if they are parking for a short time.
The message must be displayed in multiple languages for international drivers.
Mandatory Content:
Main message – in multiple languages (clearly separated or stacked):
Dutch (NL): Vergeet je ticket niet te valideren in de shop – verplicht, ook bij kort parkeren!
French (FR): N'oubliez pas de valider votre ticket à la boutique – obligatoire, même pour un court arrêt !
English (EN): Don't forget to validate your entry ticket in the shop – mandatory, even for short stops!
German (DE): Vergessen Sie nicht, Ihr Einfahrticket im Shop zu entwerten – Pflicht, auch bei kurzem Parken!
Polish (PL): Nie zapomnij zatwierdzić biletu w sklepie – obowiązkowe, nawet przy krótkim postoju!
Romanian (RO): Nu uitați să validați biletul în magazin – obligatoriu, chiar și pentru opriri scurte!
You can include more languages if space allows, but these are essential.
Opening Hours Block (in one section below):
Shop Opening Hours
Mon – Fri: 05:30 – 22:00
Sat & Sun: 08:00 – 22:00
Style & Branding:
The design must match the visual identity of Haulport 41Ter
Please refer to the attached photos of existing parking signage for guidance on colors, typography, and layout style
Our logo (attached) must be clearly visible and professionally integrated
Feel free to use icons or pictograms to visually support the message (e.g., ticket, truck, arrow)
Readability is key – large, bold text and high contrast colors that are visible from a distance
Target Audience:
International truck drivers – people who need fast, clear communication. Not everyone speaks the local language, so visual clarity and multilingual messaging are critical.
File Requirements:
Print-ready file (PDF or EPS) – 300 dpi at 1:10 scale
Include 5 cm bleed on all sides
Provide open source files if possible (AI or PSD)

```html
<!DOCTYPE html>
<html lang="en">
<head>
<meta charset="UTF-8">
<title>Haulport 41Ter – Ticket Validation Banner</title>
<link rel="stylesheet" href="https://fonts.googleapis.com/css2?family=Montserrat:wght@400;500;600;700&display=swap">
<style>
  :root {
    --navy: #1f2a5c;
    --navy-deep: #18224d;
    --blue: #1f86d4;
    --red: #d5161f;
    --white: #ffffff;
    --page: #f1f2f4;
    --sign-dark: #2b2d33;
    --shop-light: #eef0f3;
    --shop-mid: #c7ccd4;
  }
  * { margin: 0; padding: 0; box-sizing: border-box; }
  html, body {
    width: 1200px;
    height: 800px;
    overflow: hidden;
    background: var(--page);
    font-family: "Montserrat", Arial, sans-serif;
  }
  .banner {
    position: absolute;
    left: 20px;
    top: 216px;
    width: 1160px;
    height: 368px;
    background: var(--navy);
    overflow: hidden;
    color: var(--white);
  }
  .banner-shapes {
    position: absolute;
    inset: 0;
  }
  .highlight {
    background: var(--blue);
    padding: 0 6px;
  }
  .highlight--red { background: var(--red); padding: 0 4px; }

  .headline {
    position: absolute;
    left: 27px;
    top: 36px;
    font-weight: 600;
    text-transform: uppercase;
  }
  .headline__kicker {
    font-size: 24px;
    letter-spacing: 0.3px;
    line-height: 1;
  }
  .headline__main {
    margin-top: 16px;
    font-size: 42px;
    line-height: 50px;
    letter-spacing: 0.5px;
  }
  .headline__main .highlight { padding: 0 8px; }

  .hours {
    position: absolute;
    left: 27px;
    top: 236px;
  }
  .hours__title {
    font-size: 18px;
    font-weight: 600;
    line-height: 24px;
    text-transform: uppercase;
  }
  .hours__list {
    list-style: none;
    margin-top: 12px;
    font-size: 19px;
    font-weight: 400;
    line-height: 26px;
  }

  .notice {
    position: absolute;
    left: 465px;
    top: 36px;
    width: 420px;
  }
  .notice__title {
    font-size: 21px;
    font-weight: 700;
    text-transform: uppercase;
    line-height: 26px;
  }
  .notice__list {
    list-style: none;
    margin-top: 10px;
  }
  .notice__item {
    position: relative;
    padding-left: 22px;
    height: 48px;
    font-size: 13px;
    line-height: 18px;
    font-weight: 400;
  }
  .notice__item::before {
    content: "#";
    position: absolute;
    left: 0;
    top: 4px;
    font-size: 24px;
    line-height: 24px;
    font-weight: 400;
  }

  .parking-sign {
    position: absolute;
    left: 952px;
    top: 69px;
    width: 184px;
    height: 48px;
    background: var(--sign-dark);
    border-radius: 3px;
    display: flex;
    align-items: center;
    padding: 0 8px;
    gap: 10px;
  }
  .parking-sign__p {
    width: 34px;
    height: 34px;
    background: var(--blue);
    color: var(--white);
    font-weight: 700;
    font-size: 28px;
    line-height: 34px;
    text-align: center;
  }
  .parking-sign__label {
    font-size: 14px;
    font-weight: 700;
    line-height: 16px;
    text-transform: uppercase;
    flex: 1;
  }
  .parking-sign__arrow { width: 18px; height: 18px; align-self: flex-end; margin-bottom: 4px; }

  .brand-name {
    position: absolute;
    left: 956px;
    top: 276px;
    font-size: 26px;
    font-weight: 700;
    color: var(--navy);
    text-transform: uppercase;
    letter-spacing: 0.5px;
  }
</style>
</head>
<body>
  <div class="banner">
    <svg class="banner-shapes" width="1160" height="368" viewBox="0 0 1160 368" aria-hidden="false">
      <defs>
        <linearGradient id="shop-tone" x1="0" y1="0" x2="1" y2="1">
          <stop offset="0" stop-color="#f3f4f6"/>
          <stop offset="0.5" stop-color="#dfe2e7"/>
          <stop offset="1" stop-color="#c3c8d0"/>
        </linearGradient>
      </defs>
      <rect x="846" y="0" width="314" height="368" fill="url(#shop-tone)" role="img" aria-label="Photo of a brightly lit shop interior with stocked shelves"/>
      <polygon points="0,139 489,368 0,368" fill="var(--blue)"/>
      <polygon points="846,0 978,187 846,368" fill="var(--navy)"/>
      <polyline points="846,0 978,187 846,368" fill="none" stroke="#3a64b8" stroke-width="2"/>
    </svg>

    <div class="headline">
      <p class="headline__kicker">Short stop or long stay</p>
      <p class="headline__main"><span class="highlight">Ticket must</span> be<br>validated<br>in the shop.</p>
    </div>

    <div class="hours">
      <p class="hours__title">Shop <span class="highlight--red">Opening</span><br>hours.</p>
      <ul class="hours__list">
        <li>Mon – Fri: 05:30 – 22:00</li>
        <li>Sat &amp; Sun: 08:00 – 22:00</li>
      </ul>
    </div>

    <div class="notice">
      <h2 class="notice__title">Please <span class="highlight">Review carefully</span></h2>
      <ul class="notice__list">
        <li class="notice__item" lang="en">English (EN): Don't forget to validate your entry ticket in the shop – mandatory, even for short stops!</li>
        <li class="notice__item" lang="fr">French (FR): N'oubliez pas de valider votre ticket à la boutique – obligatoire, même pour un court arrêt !</li>
        <li class="notice__item" lang="nl">Dutch (NL): Vergeet je ticket niet te valideren in de shop – verplicht, ook bij kort parkeren!</li>
        <li class="notice__item" lang="de">German (DE): Vergessen Sie nicht, Ihr Einfahrticket im Shop zu entwerten – Pflicht, auch bei kurzem Parken!</li>
        <li class="notice__item" lang="pl">Polish (PL): Nie zapomnij zatwierdzić biletu w sklepie – obowiązkowe, nawet przy krótkim postoju!</li>
        <li class="notice__item" lang="ro">Romanian (RO): Nu uitați să validați biletul în magazin – obligatoriu, chiar și pentru opriri scurte!</li>
      </ul>
    </div>

    <div class="parking-sign">
      <span class="parking-sign__p">P</span>
      <span class="parking-sign__label">Parking<br>zone</span>
      <svg class="parking-sign__arrow" viewBox="0 0 18 18" aria-hidden="true">
        <path d="M3 3 L15 15 M15 6 L15 15 L6 15" fill="none" stroke="#ffffff" stroke-width="2.4"/>
      </svg>
    </div>

    <p class="brand-name">Haulport 41Ter</p>
  </div>
</body>
</html>
```